Brand new letterhead, business card, email signature etc.

We are a financial company in London, UK. Our website is www.marlowvane.com. We're wanting a complete remodel of the company colours, letter head, business cards, email signatures, etc. Looking to keep the same font for the company name. I have upload a colour palette that we want to work with. We're looking for company letterhead for outgoing letters/ correspondence, letterhead for internal documentation, email signatures, e-letters. etc. Ultimately we will redesign the entire website also. It is important that our clients get a strong, secure, warm, trustworthy, solid feeling and first impression.
Updates

Designs look the same

Target Market(s)

Institutional investors, (ultra) high net worth individuals

Industry/Entity Type

Finance, Invesments banking.

Font styles to use
Other font styles liked:
• Current font is "Champagne & Limousines"

Requirements
Must have
• Must use the colours provided on the PDF uploaded to the portal. The purple = main colour. The red = accent colour.
Nice to have
• Nice to use same font as now for the company name "Corvane". Font is "Champagne & Limousines". Nice to have some reference to the old logo flower, but only subtle.
Should not have
• Do not use the colour red from our website. Use the colours provided on the colour palette PDF that I uploaded in the portal.

```html
<!DOCTYPE html>
<html lang="en">
<head>
<meta charset="utf-8">
<title>Corvane – Business Card</title>
<link href="https://fonts.googleapis.com/css2?family=Josefin+Sans:wght@300;400&family=Montserrat:wght@400;700&display=swap" rel="stylesheet">
<style>
  :root {
    --backdrop: #222222;
    --card: #2a0e1b;
    --edge: #e23a2a;
    --copper: #8e3d1f;
    --accent: #e5402f;
    --ink: #ffffff;
  }
  * { margin: 0; padding: 0; box-sizing: border-box; }
  html, body { width: 1200px; height: 780px; overflow: hidden; background: var(--backdrop); }
  .stage { position: relative; width: 1200px; height: 780px; }

  .card {
    position: absolute;
    width: 620px;
    height: 340px;
    background: var(--card);
    border-bottom: 6px solid var(--edge);
    box-shadow: 0 18px 40px rgba(0,0,0,.55);
  }
  .card--front { left: 150px; top: 40px; }
  .card--back  { left: 430px; top: 405px; }

  .brand { display: flex; align-items: center; gap: 22px; }
  .brand__mark { width: 70px; height: 70px; border: 2px solid currentColor; }
  .brand__name {
    font-family: "Josefin Sans", sans-serif;
    font-weight: 300;
    letter-spacing: .32em;
    line-height: 1;
  }

  .card--front .brand {
    position: absolute; left: 0; right: 0; top: 50%;
    transform: translateY(-50%);
    justify-content: center;
    color: var(--copper);
  }
  .card--front .brand__mark { width: 92px; height: 92px; }
  .card--front .brand__name { font-size: 62px; }

  .card--back .brand { position: absolute; left: 36px; top: 34px; color: var(--ink); }
  .card--back .brand__mark { width: 58px; height: 58px; border-width: 1px; }
  .card--back .brand__name { font-size: 34px; }

  .contact {
    position: absolute; left: 36px; right: 36px; bottom: 30px;
    font-family: "Montserrat", sans-serif;
    color: var(--ink);
  }
  .person { font-size: 26px; font-weight: 700; margin-bottom: 12px; }
  .person__first { color: var(--accent); }
  .person__role { color: var(--accent); font-weight: 400; font-size: 20px; margin-left: 6px; }
  .contact__row { display: flex; justify-content: space-between; font-size: 13px; margin-bottom: 8px; }
  .label { color: var(--accent); margin-right: 4px; }
  .address { font-size: 13px; }
</style>
</head>
<body>
<main class="stage">
  <section class="card card--front">
    <div class="brand">
      <span class="brand__mark"></span>
      <span class="brand__name">CORVANE</span>
    </div>
  </section>

  <section class="card card--back">
    <div class="brand">
      <span class="brand__mark"></span>
      <span class="brand__name">CORVANE</span>
    </div>
    <div class="contact">
      <p class="person"><span class="person__first">Elena</span> Varkova <span class="person__role">CEO</span></p>
      <div class="contact__row">
        <span><span class="label">T:</span>(020) 555-0148</span>
        <span><span class="label">E:</span>info@marlowvane.com</span>
        <span><span class="label">W:</span>www.marlowvane.com</span>
      </div>
      <p class="address">Corvane Limited, Ashby House, Harbour Row, Kelstow, KT4 9RX</p>
    </div>
  </section>
</main>
</body>
</html>
```